Veldmark Supplies Business Card

Professional business card that stand out to our potential customers. Front and back with clean modern design

Industry/Entity Type

Oil and gas

Contact Information for Business Card

Name, address, website , office phone and cell number

Requirements
Must have
• Editable files for each employee

```html
<!DOCTYPE html>
<html lang="en">
<head>
<meta charset="utf-8">
<title>Veldmark Supplies Business Card</title>
<link rel="stylesheet" href="https://fonts.googleapis.com/css2?family=Archivo:wght@400;800&display=swap">
<style>
  :root {
    --backdrop: #3b3b3d;
    --card: #1b1b1c;
    --card-back: #121213;
    --pattern: #1c1c1e;
    --red: #ff0a12;
    --cyan: #00b4d8;
    --text: #f2f2f2;
  }
  * { margin: 0; padding: 0; box-sizing: border-box; }
  html, body { width: 1200px; height: 694px; overflow: hidden; }
  body {
    background: var(--backdrop);
    font-family: "Archivo", Arial, sans-serif;
    position: relative;
  }
  .card {
    position: absolute;
    top: 187px;
    width: 560px;
    height: 320px;
    border-radius: 22px;
    overflow: hidden;
  }
  .card--back { left: 25px; background: var(--card-back); }
  .card--front { left: 615px; background: var(--card); }

  .back-pattern {
    position: absolute; inset: 0;
    background: linear-gradient(135deg, var(--pattern), var(--card-back) 60%, var(--pattern));
  }
  .back-brand {
    position: absolute; left: 50%; top: 50%;
    transform: translate(-50%, -50%);
    display: flex; align-items: center; gap: 8px;
    color: var(--red); font-weight: 800; font-size: 15px;
    text-transform: uppercase; letter-spacing: 0.5px;
    white-space: nowrap;
  }
  .brand-mark { width: 12px; height: 12px; background: var(--cyan); flex: none; }

  .front-brand {
    position: absolute; left: 36px; top: 148px;
    display: flex; align-items: center; gap: 9px;
    color: var(--red); font-weight: 800; font-size: 19px;
    text-transform: uppercase; letter-spacing: 0.4px;
    white-space: nowrap;
  }
  .front-brand .brand-mark { width: 16px; height: 16px; }

  .divider {
    position: absolute; left: 298px; top: 50px;
    width: 1.5px; height: 200px; background: var(--red);
  }
  .contact { position: absolute; left: 322px; top: 50px; color: var(--text); }
  .contact__name { color: var(--red); font-weight: 800; font-size: 25px; line-height: 1; white-space: nowrap; }
  .contact__role { color: var(--cyan); font-size: 14px; margin-top: 4px; }
  .contact__address { font-size: 12.5px; line-height: 1.35; margin-top: 14px; white-space: nowrap; }
  .contact__list { list-style: none; margin-top: 16px; font-size: 12.5px; }
  .contact__list li { display: flex; align-items: center; gap: 9px; height: 20px; white-space: nowrap; }
  .contact__list svg { width: 13px; height: 13px; flex: none; }

  .edge-band {
    position: absolute; left: 0; right: 0; bottom: 0; height: 6px;
    background: linear-gradient(90deg, var(--red) 0 82%, var(--cyan) 82% 100%);
  }
</style>
</head>
<body>
  <section class="card card--back" aria-label="Card back">
    <div class="back-pattern" role="img" aria-label="Embossed repeating brand mark pattern on black"></div>
    <div class="back-brand"><span class="brand-mark"></span>Veldmark Supplies</div>
  </section>

  <section class="card card--front" aria-label="Card front">
    <div class="front-brand"><span class="brand-mark"></span>Veldmark Supplies</div>
    <div class="divider"></div>
    <div class="contact">
      <p class="contact__name">Daniel Rourke</p>
      <p class="contact__role">Owner</p>
      <p class="contact__address">218 Pumpjack Road, Suite 4<br>79755, Ridgeview Basin</p>
      <ul class="contact__list">
        <li><svg viewBox="0 0 16 16"><path fill="#00b4d8" d="M3 1h3l1.5 4-2 1.2a9 9 0 0 0 4.3 4.3l1.2-2 4 1.5v3a2 2 0 0 1-2 2A13 13 0 0 1 1 3a2 2 0 0 1 2-2z"/></svg>044-318 672 540</li>
        <li><svg viewBox="0 0 16 16"><rect x="4" y="1" width="8" height="14" rx="1.5" fill="none" stroke="#00b4d8" stroke-width="1.6"/><circle cx="8" cy="12.5" r="0.9" fill="#00b4d8"/></svg>044-509 287 163</li>
        <li><svg viewBox="0 0 16 16"><rect x="1" y="3" width="14" height="10" fill="#00b4d8"/><path d="M1 3l7 6 7-6" fill="none" stroke="#1b1b1c" stroke-width="1.4"/></svg>info@veldmarkmail.com</li>
        <li><svg viewBox="0 0 16 16"><circle cx="8" cy="8" r="7" fill="#00b4d8"/><path d="M1 8h14M8 1c-3 3-3 11 0 14M8 1c3 3 3 11 0 14" fill="none" stroke="#1b1b1c" stroke-width="1"/></svg>www.veldmarksupplies.com</li>
      </ul>
    </div>
    <div class="edge-band"></div>
  </section>
</body>
</html>
```